Lawn care business card

I am looking for a quality designed personal business card to represent the quality and elegant nature of our company. We separate ourselves in our market by the aesthetic value of our work, so I am looking for marketing material that does the same. We target our marketing high end customers, and we try to avoid price shoppers. I am open to all design options, so long as they are in line with our companies values.

We are tend to go with a retro look on everything from our logo and print material, to our uniforms. We like to portray and "old fashion" set of core values, with a modern elegance. So a wild and crazy look is out of the question.

Things I'd like on the card:
1.) Logo
2.) Phone number: (816) 555-2931
3.) Website: Verdelynkc.com
4.) Email: robertfairley@verdelynkc.com
5.) My name: Robert Fairley
6.) Facebook link: facebook.com/VerdelynGardenandGrounds
7.) Instagram: http://instagram.com/verdelynkc

Attached is a copy of our logo.

Reason: More time is needed to gather conclusive feedback from the members of our marketing team.

```html
<!DOCTYPE html>
<html lang="en">
<head>
<meta charset="utf-8">
<title>Verdelyn – Business Card</title>
<link rel="stylesheet" href="https://fonts.googleapis.com/css2?family=Arimo:wght@400;700&display=swap">
<style>
  :root {
    --backdrop: #e7e4df;
    --card: #ffffff;
    --band: #1f1f1f;
    --accent: #e8531f;
    --ink: #151515;
  }
  * { margin: 0; padding: 0; box-sizing: border-box; }
  html, body {
    width: 1200px;
    height: 800px;
    overflow: hidden;
    background: var(--backdrop);
    font-family: "Arimo", Arial, sans-serif;
  }
  .business-card {
    position: absolute;
    left: 75px;
    top: 100px;
    width: 1050px;
    height: 600px;
    background: var(--card);
    box-shadow: 0 6px 24px rgba(0,0,0,0.12);
    overflow: hidden;
  }
  .brand-band {
    position: absolute;
    left: 0;
    top: 240px;
    width: 100%;
    height: 72px;
    background: var(--band);
  }
  .brand-mark {
    position: absolute;
    right: 90px;
    top: 140px;
    display: flex;
    align-items: center;
    gap: 18px;
  }
  .brand-dot {
    width: 60px;
    height: 60px;
    border-radius: 50%;
    background: var(--accent);
  }
  .brand-name {
    font-size: 60px;
    font-weight: 700;
    color: var(--ink);
    letter-spacing: 1px;
    line-height: 1;
  }
  .contact-block {
    position: absolute;
    left: 330px;
    width: 620px;
    top: 330px;
    text-align: center;
    color: var(--ink);
  }
  .holder-name {
    font-size: 44px;
    font-weight: 400;
    color: var(--accent);
    letter-spacing: 0.5px;
    margin-bottom: 26px;
  }
  .contact-line {
    font-size: 23px;
    line-height: 32px;
    white-space: nowrap;
  }
</style>
</head>
<body>
  <div class="business-card">
    <div class="brand-band"></div>
    <div class="brand-mark">
      <span class="brand-dot"></span>
      <span class="brand-name">Verdelyn</span>
    </div>
    <div class="contact-block">
      <div class="holder-name">Robert Fairley</div>
      <div class="contact-line">(555) 555-2931</div>
      <div class="contact-line">Verdelynkc.com</div>
      <div class="contact-line">robertfairley@verdelynkc.com</div>
      <div class="contact-line">http://snapgrove.net/verdelynkc</div>
      <div class="contact-line">leafnook.net/VerdelynGardenandGrounds</div>
    </div>
  </div>
</body>
</html>
```